Business Card Design For A Cajun Seafood Restaurant

We are opening a cajun seafood restaurant in a week. We mainly serve cajun seafood which is orginally from Louisiana. We want design on both sides of a business card. I have menu on the website. You can go to www.reednkettle.example to check out our menu.

Restaurant name: Reed N' Kettle
Phone: +1 (555) 304-7712
Address: 48206 Ludlow Row, #7, Bexmoor Flats, Ca90000
Email: reednkettle@mailbox.example
Website: www.reednkettle.example

Maybe add social media icons (facebook, instagram) if looks nice on the business card.
facebook.com/reednkettle
instagram.com/reednkettle or @reednkettle

Attached is the logo and other business card samples that I like.

```html
<!DOCTYPE html>
<html lang="en">
<head>
<meta charset="utf-8">
<title>Reed N' Kettle — Business Card</title>
<link rel="stylesheet" href="https://fonts.googleapis.com/css2?family=Roboto:wght@300;400;500;700&display=swap">
<style>
  :root {
    --stage: #3a3a3a;
    --orange: #ff6a00;
    --card-white: #ffffff;
    --ink: #1b1b1b;
    --band: #111111;
    --yellow: #f3c300;
    --grey: #6f6f6f;
  }
  * { box-sizing: border-box; margin: 0; padding: 0; }
  html, body { width: 1200px; height: 950px; overflow: hidden; }
  body {
    background: var(--stage);
    font-family: "Roboto", Arial, sans-serif;
    position: relative;
  }
  .card {
    position: absolute;
    left: 240px;
    width: 720px;
    height: 411px;
    box-shadow: 0 10px 30px rgba(0,0,0,0.45);
    overflow: hidden;
  }
  .card--front { top: 40px; background: var(--orange); }
  .card--back { top: 499px; background: var(--card-white); }

  .brand {
    position: absolute;
    left: 0; right: 0;
    display: flex;
    align-items: center;
    justify-content: center;
    gap: 14px;
  }
  .brand__mark {
    width: 26px; height: 26px;
    border-radius: 50%;
    background: var(--ink);
  }
  .brand__name {
    font-weight: 700;
    font-size: 44px;
    color: var(--ink);
    letter-spacing: 1px;
  }
  .card--front .brand { top: 150px; }
  .front__tagline {
    position: absolute;
    top: 215px; left: 0; right: 0;
    text-align: center;
    font-size: 17px;
    font-weight: 500;
    letter-spacing: 2px;
    color: var(--ink);
    text-transform: uppercase;
  }
  .front__social {
    position: absolute;
    top: 300px; left: 0; right: 0;
    display: flex;
    justify-content: center;
    gap: 26px;
    font-size: 15px;
    color: var(--ink);
  }
  .social-item { display: flex; align-items: center; gap: 7px; }
  .social-item__box {
    width: 13px; height: 13px;
    background: var(--ink);
    border-radius: 2px;
  }

  .card--back .brand { top: 96px; }
  .card--back .brand__name { font-size: 40px; }
  .back__tagline {
    position: absolute;
    top: 150px; left: 0; right: 0;
    text-align: center;
    font-size: 14px;
    font-weight: 500;
    letter-spacing: 2px;
    color: var(--ink);
    text-transform: uppercase;
  }
  .name-band {
    position: absolute;
    top: 182px; left: 0; right: 0;
    height: 46px;
    background: var(--band);
    display: flex;
    align-items: center;
    justify-content: center;
    font-size: 21px;
    font-weight: 500;
  }
  .name-band__name { color: var(--orange); }
  .name-band__role { color: var(--yellow); }
  .contact {
    position: absolute;
    top: 248px; left: 0; right: 0;
    text-align: center;
    color: var(--grey);
    font-size: 16px;
    font-weight: 300;
    line-height: 27px;
  }
  .contact__label { color: var(--orange); font-weight: 500; }
  .contact__web { letter-spacing: 4px; font-weight: 400; }
  .foot-band {
    position: absolute;
    bottom: 22px; left: 0; right: 0;
    height: 14px;
    background: var(--band);
  }
</style>
</head>
<body>
  <section class="card card--front" aria-label="Card front">
    <div class="brand">
      <span class="brand__mark"></span>
      <span class="brand__name">Reed N' Kettle</span>
    </div>
    <p class="front__tagline">Cajun Seafood House</p>
    <div class="front__social">
      <span class="social-item"><span class="social-item__box"></span>reednkettle</span>
      <span class="social-item"><span class="social-item__box"></span>@reednkettle</span>
    </div>
  </section>

  <section class="card card--back" aria-label="Card back">
    <div class="brand">
      <span class="brand__mark"></span>
      <span class="brand__name">Reed N' Kettle</span>
    </div>
    <p class="back__tagline">Cajun Seafood House</p>
    <div class="name-band">
      <span class="name-band__name">Sam Harlow</span>
      <span class="name-band__role">&nbsp;-&nbsp;President</span>
    </div>
    <div class="contact">
      <p>48206 Ludlow Row, #7, Bexmoor Flats, Ca90000</p>
      <p><span class="contact__label">P:</span> +1 (555) 304-7712 &nbsp;<span class="contact__label">E:</span> reednkettle@mailbox.example</p>
      <p class="contact__web">www.reednkettle.example</p>
    </div>
    <div class="foot-band"></div>
  </section>
</body>
</html>
```